Design a cover that embodies the concept of healing by Walking Out of Shadows

Subtitle: How to use tapping, applied kinesiology, and Chinese medicine to heal your body, free your mind and live in peace.

Tapping (Emotional Freedom Technique) is a modern mix of psychology and Chinese medicine that helps people to release the emotions they have inside that are contributing to the depression and anxiety they feel. Applied kinesiology or muscle testing is a biofeedback tool which helps to extract information from the body that can help people to profoundly heal. It can be used to determine whether heavy metals, heavy chemicals, food sensitivities or pathogens are causing the body problems. It can also be used to determine which supplements can help someone heal. This tool also can be used to identify emotions and memories that are also causing someone problems. Lastly, Chinese medicine uses food therapy, herbal formulas, meditation, tai chi (meditative movement), cupping and other tools to help people to be free of depression. This book is written to be information but also details my own personal journey of how I was able to heal from 11 years of heavy depression through the use of these tools.

The heart of the book is about emotional release, emotional freedom and emotional healing. You can surrender, release or let go of emotions and feel better very quickly. This certainly was my experience.

I would like the front and back cover to each be 8.5" x 5.5". I still have to get an ISBN number for the back page as well. Here is the text that I would like on the back cover for now: Millions of people feel the pain, loneliness, and agony of anxiety and depression every day. Many turn to Western medicine in the hopes that a pill will ease the pain and make the problem go away. Oftentimes, this only makes matters worse and doesn’t address the root cause. No one should have to struggle like this when natural answers exist that can address the physical, energetic, emotional, or spiritual causes of anxiety and depression. For 11 long years, Dr. Mervin personally struggled with heavy depression until he discovered answers that helped him to completely heal. Walking Out of Shadows is a guide that will help you discover - The two root physical causes of depression and exactly what to do to start healing today - How the negative emotions we have stored within from trauma and bad experiences can drive depression - Tools from Chinese medicine, applied kinesiology, and tapping to help you free your mind and live in peace - An actionable plan to help you let go of the pain, suffering, and negative emotions from your past Whether you feel depressed and anxious or know someone who struggles with these issues, Walking Out of Shadows will transform how you think about depression and will give you the tools to heal so that you can be free and live in peace. Dr. Mervin Holloway is a board-certified acupuncture physician licensed in the state of Florida. He received his training at the Marlow Institute of Restorative Health. He also graduated with a master’s degree in counseling and psychology from Cedarbrook School of Ministry. His mission is to help people transform their health and improve the quality of their life naturally. He lives in Orlando, FL where he runs a holistic medical clinic called Brightpath Wellness Center. www.drmervinholloway.example Instagram: drmervinholloway Facebook: brightpathwellnesscenter

Target Market(s)

Those who suffer from depression and anxiety and want to heal naturally

Industry/Entity Type

Health And Wellness

Requirements
Must have
• My picture should be small and go on the back cover next to the information about me. The front cover would be all graphical. Thank you. On the front cover my name should be posted as "Dr. Mervin Holloway, AP, MA"

```html
<!DOCTYPE html>
<html lang="en">
<head>
<meta charset="utf-8">
<title>Walking Out of Shadows — Cover</title>
<link href="https://fonts.googleapis.com/css2?family=Open+Sans:wght@400;600;700;800&display=swap" rel="stylesheet">
<style>
  :root {
    --paper: #ffffff;
    --wine: #7d1f2c;
    --wine-deep: #5a1320;
    --wine-soft: #a44a56;
    --ink: #111111;
    --text: #2a2a2a;
    --photo-scarf: rgba(150, 40, 56, 0.55);
    --photo-sweater: rgba(235, 225, 225, 0.9);
  }
  * { margin: 0; padding: 0; box-sizing: border-box; }
  html, body {
    width: 879px; height: 1200px; overflow: hidden;
    background: var(--paper);
  }
  .cover {
    position: relative; width: 879px; height: 1200px;
    background: var(--paper);
    font-family: "Open Sans", Arial, sans-serif;
    overflow: hidden;
  }
  .title {
    position: absolute; left: 0; right: 0; top: 70px;
    text-align: center; color: var(--wine);
    font-weight: 700; text-transform: uppercase;
    text-shadow: 2px 3px 2px rgba(90, 19, 32, 0.35);
  }
  .title span { display: block; }
  .title-line-one { font-size: 78px; line-height: 1; letter-spacing: 1px; }
  .title-of {
    display: flex !important; align-items: center; justify-content: center;
    gap: 18px; font-size: 58px; line-height: 1; margin-top: 6px;
  }
  .title-of .rule {
    display: block; width: 230px; height: 3px;
    background: linear-gradient(90deg, rgba(125,31,44,0), var(--wine));
  }
  .title-of .rule.right {
    background: linear-gradient(90deg, var(--wine), rgba(125,31,44,0));
  }
  .title-main { font-size: 128px; line-height: 1.05; letter-spacing: 2px; }
  .subtitle {
    position: absolute; left: 110px; right: 110px; top: 420px;
    text-align: center; color: var(--text);
    font-size: 29px; line-height: 1.35; font-weight: 400;
  }
  .subtitle .accent { color: var(--wine); font-weight: 700; }
  .portrait {
    position: absolute; left: 400px; top: 600px; width: 479px; height: 470px;
    background:
      radial-gradient(ellipse 38% 30% at 42% 22%, rgba(225, 190, 180, 0.8), rgba(225,190,180,0) 100%),
      radial-gradient(ellipse 55% 55% at 62% 62%, var(--photo-scarf), rgba(150,40,56,0) 100%),
      radial-gradient(ellipse 70% 60% at 40% 75%, var(--photo-sweater), rgba(235,225,225,0) 100%);
    -webkit-mask-image: linear-gradient(180deg, #000 70%, transparent 100%);
            mask-image: linear-gradient(180deg, #000 70%, transparent 100%);
  }
  .tapping-lines { position: absolute; left: 0; top: 0; }
  .author {
    position: absolute; right: 40px; bottom: 42px;
    font-size: 40px; font-weight: 800; color: var(--ink);
    white-space: nowrap;
  }
</style>
</head>
<body>
  <main class="cover">
    <h1 class="title">
      <span class="title-line-one">Walking Out</span>
      <span class="title-of"><span class="rule"></span>Of<span class="rule right"></span></span>
      <span class="title-main">Shadows</span>
    </h1>

    <p class="subtitle">How to use tapping, applied kinesiology, and Chinese medicine to heal your body, free your mind and live in <span class="accent">peace</span></p>

    <div class="portrait" role="img" aria-label="Cut-out photo of a smiling person with raised fists, wearing a red patterned scarf and white sweater, fading into the white page"></div>

    <svg class="tapping-lines" width="879" height="1200" viewBox="0 0 879 1200" aria-hidden="true">
      <g stroke="#8a2a36" stroke-width="3" stroke-linecap="round">
        <line x1="220" y1="640" x2="879" y2="640" stroke-opacity="0.7"/>
        <line x1="300" y1="690" x2="879" y2="690" stroke-opacity="0.75"/>
        <line x1="180" y1="735" x2="879" y2="735" stroke-opacity="0.55"/>
        <line x1="250" y1="778" x2="879" y2="778" stroke-opacity="0.5"/>
      </g>
    </svg>

    <p class="author">Dr. Mervin Holloway, AP, MA</p>
  </main>
</body>
</html>
```